business card - Helicopter Flight Services, Flight School, etc.

We need a business card design for a new helicopter service.

We offer Helicopter Flight Services, Aerial Filming & Photography, Flight School, and Helicopter Tours. In that order.

Summit BladeAir, Inc.
Dennis Tollerby
SummitBladeair@Kestmail.com
626-418-7352

Based at the Brenwick Airport in Van Nuys, CA. The final design should communicate integrity and safety. Pictures or logos at your discretion.

Card back side - surprise me.

```html
<!DOCTYPE html>
<html lang="en">
<head>
<meta charset="utf-8">
<title>Summit BladeAir, Inc. — Business Card</title>
<link href="https://fonts.googleapis.com/css2?family=Open+Sans:wght@400;600;700&display=swap" rel="stylesheet">
<style>
  :root {
    --page: #e9e6e1;
    --card-black: #0b0b0c;
    --card-black-soft: #1a1b1e;
    --brand-blue: #1f86d6;
    --brand-blue-deep: #0f5fa8;
    --brand-blue-light: #39a8e8;
    --text-white: #ffffff;
    --text-soft: #d8dde3;
    --grass: #a98f5e;
    --grass-dark: #6d5a38;
    --sky: #8fb8d8;
    --sky-light: #c9dbe8;
  }
  * { margin: 0; padding: 0; box-sizing: border-box; }
  html, body {
    width: 1200px; height: 913px; overflow: hidden;
    background: var(--page);
    font-family: "Open Sans", Arial, sans-serif;
  }
  .canvas {
    position: relative; width: 1200px; height: 913px;
    display: flex; align-items: center; justify-content: center; gap: 60px;
  }
  .card {
    position: relative; width: 520px; height: 297px; overflow: hidden;
    background: linear-gradient(160deg, var(--card-black-soft), var(--card-black) 60%);
    box-shadow: 0 10px 28px rgba(0,0,0,0.25);
  }

  /* Front */
  .front__band {
    position: absolute; left: 0; top: 0; width: 168px; height: 100%;
    background: linear-gradient(180deg, var(--brand-blue-light), var(--brand-blue) 45%, var(--brand-blue-deep));
  }
  .front__brand-name {
    position: absolute; left: 190px; top: 52px;
    color: var(--brand-blue-light); font-weight: 700; font-size: 26px;
    letter-spacing: 0.3px; white-space: nowrap; line-height: 1.2;
  }
  .front__contact {
    position: absolute; left: 190px; bottom: 50px; color: var(--text-white);
  }
  .front__name { font-weight: 700; font-size: 22px; line-height: 1.1; }
  .front__role { color: var(--brand-blue-light); font-size: 14px; margin: 2px 0 10px; }
  .front__line {
    display: flex; align-items: center; gap: 8px; font-size: 14px; color: var(--text-soft); line-height: 1.5;
  }
  .front__line svg { width: 13px; height: 13px; flex: none; }

  /* Back */
  .back__photo { position: absolute; top: 0; height: 136px; }
  .back__photo--field {
    left: 0; width: 270px;
    background: linear-gradient(170deg, #8a7b5a, var(--grass) 45%, var(--grass-dark));
  }
  .back__photo--sky {
    left: 270px; width: 250px;
    background: linear-gradient(180deg, var(--sky-light), var(--sky) 60%, #b59a8a);
  }
  .back__services {
    position: absolute; left: 36px; bottom: 30px; list-style: none;
    color: var(--text-white); font-size: 16px; line-height: 1.5;
  }
  .back__services li { display: flex; align-items: center; gap: 12px; }
  .back__services li::before {
    content: ""; width: 10px; height: 10px; border-radius: 50%; background: var(--brand-blue);
  }
</style>
</head>
<body>
  <main class="canvas">
    <section class="card front" aria-label="Card front">
      <div class="front__band"></div>
      <p class="front__brand-name">Summit BladeAir, Inc.</p>
      <div class="front__contact">
        <p class="front__name">Dennis Tollerby</p>
        <p class="front__role">Owner</p>
        <p class="front__line">
          <svg viewBox="0 0 24 24" fill="var(--brand-blue-light)"><path d="M6.6 10.8a15.1 15.1 0 0 0 6.6 6.6l2.2-2.2a1 1 0 0 1 1-.25 11.4 11.4 0 0 0 3.6.57 1 1 0 0 1 1 1V20a1 1 0 0 1-1 1A17 17 0 0 1 3 4a1 1 0 0 1 1-1h3.5a1 1 0 0 1 1 1c0 1.25.2 2.45.57 3.6a1 1 0 0 1-.25 1z"/></svg>
          626-418-7352
        </p>
        <p class="front__line">
          <svg viewBox="0 0 24 24" fill="none" stroke="var(--brand-blue-light)" stroke-width="2.4"><rect x="2" y="5" width="20" height="14" rx="1"/><path d="M2 6l10 7 10-7"/></svg>
          SummitBladeair@Kestmail.com
        </p>
      </div>
    </section>

    <section class="card back" aria-label="Card back">
      <div class="back__photo back__photo--field" role="img" aria-label="Photo: pilot and passenger beside a helicopter in a dry grass field"></div>
      <div class="back__photo back__photo--sky" role="img" aria-label="Photo: helicopter flying over hills against a blue sky"></div>
      <ul class="back__services">
        <li>Helicopter Flight Services</li>
        <li>Aerial Filming &amp; Photography</li>
        <li>Flight School</li>
        <li>Helicopter Tours</li>
      </ul>
    </section>
  </main>
</body>
</html>
```